Business Card - connecting 2 souls and beggining the journey of self discovery

Logo on the front
with tag line

On the back list of services and contact details

Seminars
workshops
Coaching
podcasts

Darren Whitlow
Health & Wellbeing Life Coach
0491 372 615
darren@brightcoreliving.example
brightcoreliving.example

Industry/Entity Type

Life Coaching

Contact Information for Business Card

I like the use of colour from the logo to be used. I'm not a fan of white.

Requirements
Must have
• My tagline: The journey home starts with you
Nice to have
• Use of colour that is in the mind body soul logo

```html
<!DOCTYPE html>
<html lang="en">
<head>
<meta charset="utf-8">
<title>Brightcore Living – Business Card</title>
<link href="https://fonts.googleapis.com/css2?family=Montserrat:wght@500&family=Open+Sans:wght@600&family=Roboto:wght@400&family=Roboto+Condensed:wght@700&display=swap" rel="stylesheet">
<style>
  :root {
    --backdrop: #2a2a2a;
    --paper: #f4f4f3;
    --ink-grey: #7a7a7a;
    --ink-dark: #4f4f4f;
    --leaf: #5bb58a;
    --coral: #ef5b6c;
    --lime: #8cc152;
    --teal: #52ad8c;
    --peach: #f6a05c;
    --logo-disc: #f2a65a;
    --white: #ffffff;
  }
  * { margin: 0; padding: 0; box-sizing: border-box; }
  html, body { width: 1200px; height: 960px; overflow: hidden; }
  body { background: var(--backdrop); position: relative; font-family: "Roboto", Arial, sans-serif; }

  .card { position: absolute; width: 600px; height: 342px; border-radius: 22px; overflow: hidden; }

  /* Front */
  .card-front { left: 314px; top: 113px; background: var(--paper); }
  .front-stripe { position: absolute; left: 0; right: 0; top: 325px; height: 3px;
    background: linear-gradient(90deg, var(--coral), var(--peach), var(--coral)); }
  .front-band { position: absolute; left: 0; right: 0; top: 328px; bottom: 0;
    background: linear-gradient(90deg, var(--teal), var(--lime) 50%, var(--teal)); }

  .brand-block { position: absolute; left: 20px; width: 268px; top: 98px; text-align: center; }
  .brand-mark { display: block; margin: 0 auto; width: 78px; height: 78px; border-radius: 50%; background: var(--logo-disc); }
  .brand-name { margin-top: 16px; font-family: "Montserrat", Arial, sans-serif; font-weight: 500;
    font-size: 19.5px; letter-spacing: -0.6px; color: var(--ink-grey); line-height: 1; }
  .brand-tagline { margin-top: 5px; font-family: "Open Sans", Arial, sans-serif; font-weight: 600;
    font-size: 13.5px; color: var(--ink-grey); line-height: 1; }

  .divider { position: absolute; left: 285px; top: 100px; width: 1px; height: 142px;
    background: linear-gradient(180deg, transparent, #9a9a9a 15%, #9a9a9a 85%, transparent); }

  .person { position: absolute; left: 307px; top: 111px; }
  .person-name { font-family: "Roboto Condensed", Arial, sans-serif; font-weight: 700; font-size: 21.5px;
    color: var(--leaf); text-transform: uppercase; line-height: 1; }
  .person-role { margin-top: 6px; font-family: "Roboto", Arial, sans-serif; font-size: 15px;
    color: var(--coral); text-transform: uppercase; letter-spacing: 0.2px; line-height: 1; }

  .contacts { position: absolute; left: 307px; top: 175px; list-style: none; }
  .contacts li { display: flex; align-items: center; height: 19px; font-size: 14.5px; color: var(--ink-dark); }
  .contacts svg { width: 13px; height: 13px; margin-right: 9px; fill: var(--leaf); flex: none; }

  /* Back */
  .card-back { left: 311px; top: 472px;
    background: radial-gradient(ellipse 60% 70% at 50% 35%, var(--lime), var(--teal)); }
  .back-mark { position: absolute; left: 247px; top: 92px; width: 108px; height: 108px; border-radius: 50%; background: var(--logo-disc); }
  .back-name { position: absolute; left: 0; right: 0; top: 224px; text-align: center;
    font-family: "Montserrat", Arial, sans-serif; font-weight: 500; font-size: 28px; letter-spacing: -0.9px;
    color: var(--white); line-height: 1; }
  .services { position: absolute; left: 0; right: 0; top: 288px; text-align: center; list-style: none;
    font-size: 15px; color: var(--white); line-height: 1; }
  .services li { display: inline; }
  .services li + li::before { content: "•"; margin: 0 5px 0 3px; font-size: 11px; }
</style>
</head>
<body>

<section class="card card-front" aria-label="Business card front">
  <div class="brand-block">
    <span class="brand-mark" aria-hidden="true"></span>
    <p class="brand-name">Brightcore Living</p>
    <p class="brand-tagline">The journey home starts with you</p>
  </div>
  <div class="divider"></div>
  <div class="person">
    <h1 class="person-name">Darren Whitlow</h1>
    <p class="person-role">Health &amp; Wellbeing Life Coach</p>
  </div>
  <ul class="contacts">
    <li><svg viewBox="0 0 24 24" aria-hidden="true"><path d="M6.6 10.8a15.1 15.1 0 0 0 6.6 6.6l2.2-2.2c.3-.3.7-.4 1-.2 1.1.4 2.3.6 3.6.6.6 0 1 .4 1 1V20c0 .6-.4 1-1 1A17 17 0 0 1 3 4c0-.6.4-1 1-1h3.5c.6 0 1 .4 1 1 0 1.3.2 2.5.6 3.6.1.3 0 .7-.2 1z"/></svg>0491 372 615</li>
    <li><svg viewBox="0 0 24 24" aria-hidden="true"><path d="M2 5h20v14H2z M4 7v.5l8 5 8-5V7l-8 5z" fill-rule="evenodd"/></svg>darren@brightcoreliving.example</li>
    <li><svg viewBox="0 0 24 24" aria-hidden="true"><circle cx="12" cy="12" r="10"/><path d="M2 12h20M12 2c3 3 3 17 0 20M12 2c-3 3-3 17 0 20" stroke="#f4f4f3" stroke-width="1.6" fill="none"/></svg>www.brightcoreliving.example</li>
  </ul>
  <div class="front-stripe"></div>
  <div class="front-band"></div>
</section>

<section class="card card-back" aria-label="Business card back">
  <span class="back-mark" aria-hidden="true"></span>
  <p class="back-name">Brightcore Living</p>
  <ul class="services">
    <li>Seminars</li><li>Workshops</li><li>Coaching</li><li>Podcasts</li>
  </ul>
</section>

</body>
</html>
```